business card deign

Logo needs the following on it.
1. attached logo
2. Tagline - "If it keeps a drink cold or the party going...we do it!"
3. Name- Dalton Pikes, Founder and CPO
4. Address - 412 E. Carver Avenue, Ste 2207, Tampa, FL. 33917
5. Phone - 555.318.4726

```html
<!DOCTYPE html>
<html lang="en">
<head>
<meta charset="UTF-8">
<title>Chillvale Business Card</title>
<link rel="stylesheet" href="https://fonts.googleapis.com/css2?family=Roboto:wght@400;500;700&display=swap">
<style>
  :root {
    --page-bg: #e4e4e4;
    --card-black: #151515;
    --card-white: #ffffff;
    --ink: #111111;
    --ink-soft: #222222;
  }
  * { box-sizing: border-box; margin: 0; padding: 0; }
  html, body {
    width: 1200px; height: 711px; overflow: hidden;
    background: var(--page-bg);
    font-family: "Roboto", Arial, sans-serif;
  }
  .stage { position: relative; width: 1200px; height: 711px; }
  .card {
    position: absolute; top: 205px;
    width: 525px; height: 300px;
    border-radius: 26px; overflow: hidden;
  }
  .card-back { left: 50px; background: var(--card-black); }
  .card-front { left: 625px; background: var(--card-white); }

  .back-brand {
    position: absolute; inset: 0;
    display: flex; flex-direction: column; align-items: center; justify-content: center; gap: 22px;
  }
  .brand-dot { width: 58px; height: 58px; border-radius: 50%; background: var(--card-white); }
  .brand-name-large {
    color: var(--card-white); font-weight: 700; font-size: 34px; letter-spacing: 14px;
    padding-left: 14px;
  }

  .front-panel { position: absolute; inset: 0; width: 525px; height: 300px; }

  .front-content { position: absolute; left: 34px; top: 30px; width: 280px; color: var(--ink); }
  .brand-row { display: flex; align-items: center; gap: 10px; margin-bottom: 22px; }
  .brand-square { width: 22px; height: 22px; background: var(--ink); }
  .brand-name-small { font-weight: 700; font-size: 18px; letter-spacing: 6px; }

  .person { position: relative; }
  .accent-bar {
    position: absolute; left: -34px; top: 4px; width: 14px; height: 46px; background: var(--ink);
  }
  .person-name { font-weight: 700; font-size: 25px; line-height: 1.1; }
  .person-title { font-size: 14px; font-weight: 500; margin-top: 3px; }

  .tagline { font-size: 12px; line-height: 1.45; margin-top: 12px; color: var(--ink-soft); }

  .contact { list-style: none; margin-top: 12px; font-size: 12px; color: var(--ink-soft); }
  .contact li { display: flex; align-items: flex-start; gap: 8px; line-height: 1.45; margin-bottom: 3px; }
  .contact svg { flex: none; margin-top: 2px; }
</style>
</head>
<body>
<main class="stage">
  <section class="card card-back" aria-label="Card back">
    <div class="back-brand">
      <span class="brand-dot"></span>
      <span class="brand-name-large">CHILLVALE</span>
    </div>
  </section>

  <section class="card card-front" aria-label="Card front">
    <svg class="front-panel" viewBox="0 0 525 300" role="img" aria-label="Large brand emblem area on black panel">
      <path d="M525 0 L320 0 C340 40 300 70 290 110 C280 160 300 200 265 240 C245 265 250 285 240 300 L525 300 Z" fill="var(--card-black)"/>
    </svg>

    <div class="front-content">
      <div class="brand-row">
        <span class="brand-square"></span>
        <span class="brand-name-small">CHILLVALE</span>
      </div>

      <div class="person">
        <span class="accent-bar"></span>
        <h1 class="person-name">Dalton Pikes</h1>
        <p class="person-title">Founder and CPO</p>
      </div>

      <p class="tagline">If it keeps a drink cold or<br>the party going...we do it!</p>

      <ul class="contact">
        <li>
          <svg width="12" height="12" viewBox="0 0 24 24" aria-hidden="true"><path fill="var(--ink)" d="M6.6 10.8a15 15 0 0 0 6.6 6.6l2.2-2.2c.3-.3.7-.4 1-.2 1.1.4 2.3.6 3.6.6.6 0 1 .4 1 1V20c0 .6-.4 1-1 1C10.6 21 3 13.4 3 4c0-.6.4-1 1-1h3.5c.6 0 1 .4 1 1 0 1.3.2 2.5.6 3.6.1.3 0 .7-.2 1z"/></svg>
          <span>555.318.4726</span>
        </li>
        <li>
          <svg width="12" height="14" viewBox="0 0 24 28" aria-hidden="true"><path fill="var(--ink)" d="M12 1a8 8 0 0 0-8 8c0 6 8 15 8 15s8-9 8-15a8 8 0 0 0-8-8zm0 11a3 3 0 1 1 0-6 3 3 0 0 1 0 6z"/></svg>
          <span>412 E. Carver Avenue,<br>Ste 2207, Tampa, FL. 33917</span>
        </li>
      </ul>
    </div>
  </section>
</main>
</body>
</html>
```